Small legal and financial translation company needs Squarespace website, brochure and logo

Hello,
We are Lumarin Services (www.lumarinservices-example.com), a boutique legal and financial translation company. We offer our services mainly to Spanish customers. Our primary line of business is the translation of financial statements, but we translate a wide variety legal and financial texts.
The project we are offering comprises three parts: a redo of the current website, an informational brochure for potential customer and a logo design. These three parts should provide a consistent image. We would develop content soon.
We are looking for a website that would look like a typical law firm website, nothing too fancy. Right now, it is in English, Spanish and French, although the new site need only be in English and Spanish. There must be good toggling between the English and Spanish versions. There would be no need for tie-ins to social media and it would not contain a blog. Basically, a static site. We aren't interesting in driving traffic to the site or SEO, as we will contact nearly all potential customers beforehand. The website must be built in Squarespace to enable a smooth transition. The content would be similar to the current page, we'll be working on the exact content, but a rough draft is attached.
The brochure will be some three pages and would introduce the company to potential customers, using similar images as the website and the logo to be designed.
The only specifications for the logo is, as the website and brochure, it convey a sense of security and trust.
Feel free to ask with any questions as this is the first time we have used this platform.
Thank you!
Updates

I've added a more or less final version for the text in the brochure and updated the brief. Added Wednesday, June 10, 2015

Target Market(s)

Spanish law firms, auditors, accountants, banks, investment firms

Industry/Entity Type

Finance

Logo Text

Lumarin Services

Number of Pages Required

5+ page

Font styles to use
Serif

Requirements
Must have
• The website must be built in Squarespace and have a good option to toggle between English and Spanish versions.
• Brochure must be in both English and Spanish, I'm attaching a rough draft of the information that it will probably have. This should give an idea about what to include and the spacing. I will update it to include the final information.
Nice to have
• Would be nice to have some quality finance- and legal-related images
Should not have
• Vibrant colours

```html
<!DOCTYPE html>
<html lang="en">
<head>
<meta charset="utf-8">
<title>Lumarin Services – Brochure Pages 5 &amp; 6</title>
<link rel="stylesheet" href="https://fonts.googleapis.com/css2?family=Cinzel:wght@500;600&family=Crimson+Text:ital,wght@0,400;1,600&family=Arimo:wght@400;700&display=swap">
<style>
:root{
  --backdrop:#e4e4e4;
  --paper:#ffffff;
  --burgundy:#7a0d1c;
  --burgundy-light:#9a1a2c;
  --ink:#2a2a2a;
  --muted:#666666;
  --table-light:#e9e9ea;
  --table-mid:#d2d3d5;
  --table-line:#f4f4f4;
  --rule:#bdbdbd;
  --black:#111111;
}
*{box-sizing:border-box;margin:0;padding:0}
html,body{width:1200px;height:847px;overflow:hidden}
body{background:var(--backdrop);display:flex;align-items:center;justify-content:center;font-family:"Crimson Text",serif;color:var(--ink)}
.spread{display:flex;width:960px;height:620px;box-shadow:0 18px 40px rgba(0,0,0,.25)}
.page{position:relative;width:480px;height:620px;background:var(--paper);overflow:hidden}
.page--left{border-right:1px solid #dcdcdc}
.page-title{font-family:"Cinzel",serif;font-weight:600;color:var(--burgundy);font-size:19px;letter-spacing:.5px}
.page--left .page-title{position:absolute;left:22px;top:38px}
.page--right .page-title{position:absolute;left:28px;top:24px}

/* pricing table */
.pricing{position:absolute;left:22px;top:74px;width:436px;border-collapse:collapse;
  background:linear-gradient(90deg,var(--table-mid),var(--table-light) 45%,var(--table-mid))}
.pricing th{font-family:"Crimson Text",serif;font-weight:600;font-size:11px;height:28px;color:var(--ink)}
.pricing td{height:49px;border-top:1px solid var(--table-line);font-size:11.5px;color:var(--muted)}
.pricing .service{width:160px;padding-left:14px;line-height:1.15;font-size:10.5px}
.pricing .price{text-align:center;border-left:1px solid var(--table-line)}
.pricing th.col-standard,.pricing .price--standard{background:rgba(255,255,255,.25)}

/* clients */
.intro{position:absolute;left:28px;top:56px;width:420px;font-size:10.5px;line-height:1.25;color:var(--muted)}
.testimonial{position:absolute;left:28px;width:428px;height:138px;display:flex;gap:14px}
.testimonial + .testimonial{border-top:1px solid var(--rule)}
.client{width:110px;display:flex;flex-direction:column;align-items:center;padding-top:12px}
.client-photo{width:86px;height:86px;border-radius:50%;background:radial-gradient(circle at 50% 40%,#c79a82,#6b4a3a 70%,#3a2a22)}
.client-name{font-family:"Arimo",sans-serif;font-size:11.5px;margin-top:8px;color:var(--black)}
.quote{position:relative;flex:1;padding:14px 16px 0 20px;font-style:italic;font-weight:600;font-size:10.8px;line-height:1.28;text-align:justify;color:var(--ink)}
.quote::before,.quote::after{font-family:Georgia,serif;font-style:normal;font-weight:700;font-size:26px;position:absolute;color:var(--black);line-height:1}
.quote::before{content:"\201C";left:0;top:10px}
.quote::after{content:"\201D";right:0;bottom:-4px}

/* footer band */
.band{position:absolute;left:0;bottom:0;width:480px;height:100px}
.band-url{position:absolute;left:24px;bottom:22px;font-family:"Crimson Text",serif;font-size:16px;color:#fff;letter-spacing:.3px}
</style>
</head>
<body>
<main class="spread">
  <section class="page page--left">
    <h2 class="page-title">Translation Pricing</h2>
    <table class="pricing">
      <thead><tr><th></th><th class="col-standard">Standard</th><th>Advance</th></tr></thead>
      <tbody>
        <tr><td class="service">Lorem ipsum dolor sit amet, consectetuer adipiscing elit</td><td class="price price--standard">$100</td><td class="price">$200</td></tr>
        <tr><td class="service">Lorem ipsum dolor sit amet, consectetuer adipiscing elit</td><td class="price price--standard">$100</td><td class="price">$200</td></tr>
        <tr><td class="service">Lorem ipsum dolor sit amet, consectetuer adipiscing elit</td><td class="price price--standard">$100</td><td class="price">$200</td></tr>
        <tr><td class="service">Lorem ipsum dolor sit amet, consectetuer adipiscing elit</td><td class="price price--standard">$100</td><td class="price">$200</td></tr>
        <tr><td class="service">Lorem ipsum dolor sit amet, consectetuer adipiscing elit</td><td class="price price--standard">$100</td><td class="price">$200</td></tr>
        <tr><td class="service">Lorem ipsum dolor sit amet, consectetuer adipiscing elit</td><td class="price price--standard">$100</td><td class="price">$200</td></tr>
        <tr><td class="service">Lorem ipsum dolor sit amet, consectetuer adipiscing elit</td><td class="price price--standard">$100</td><td class="price">$200</td></tr>
        <tr><td class="service">Lorem ipsum dolor sit amet, consectetuer adipiscing elit</td><td class="price price--standard">$100</td><td class="price">$200</td></tr>
        <tr><td class="service">Lorem ipsum dolor sit amet, consectetuer adipiscing elit</td><td class="price price--standard">$100</td><td class="price">$200</td></tr>
      </tbody>
    </table>
    <svg class="band" viewBox="0 0 480 100" aria-hidden="true">
      <defs><linearGradient id="bandRedL" x1="0" x2="1"><stop offset="0" stop-color="#7a0d1c"/><stop offset="1" stop-color="#9a1a2c"/></linearGradient></defs>
      <polygon points="0,38 480,38 480,100 0,100" fill="url(#bandRedL)"/>
      <polygon points="300,38 480,14 480,38" fill="#111"/>
    </svg>
    <p class="band-url">www.lumarinservices-example.com</p>
  </section>

  <section class="page page--right">
    <h2 class="page-title">Our Clients</h2>
    <p class="intro">Lorem ipsum dolor sit amet, consectetuer adipiscing elit, sed diam nonummy nibh euismod tincidunt ut laoreet dolore magna aliquam erat volutpat</p>

    <article class="testimonial" style="top:96px">
      <div class="client"><div class="client-photo" role="img" aria-label="Portrait photo of client Daniel Reyes"></div><p class="client-name">Mr. Daniel Reyes</p></div>
      <blockquote class="quote">Lorem ipsum dolor sit amet, consectetuer adipiscing elit, sed diam nonummy nibh euismod tincidunt ut laoreet dolore magna aliquam erat volutpat. Ut wisi enim ad minim veniam, quis nostrud exerci tation ullamcorper suscipit lobortis nisl ut aliquip ex ea commodo consequat. Duis autem vel eum iriure dolor in hendrerit in vulputate velit esse molestie consequat, vel illum</blockquote>
    </article>
    <article class="testimonial" style="top:234px">
      <div class="client"><div class="client-photo" role="img" aria-label="Portrait photo of client Daniel Reyes"></div><p class="client-name">Mr. Daniel Reyes</p></div>
      <blockquote class="quote">Lorem ipsum dolor sit amet, consectetuer adipiscing elit, sed diam nonummy nibh euismod tincidunt ut laoreet dolore magna aliquam erat volutpat. Ut wisi enim ad minim veniam, quis nostrud exerci tation ullamcorper suscipit lobortis nisl ut aliquip ex ea commodo consequat. Duis autem vel eum iriure dolor in hendrerit in vulputate velit esse molestie consequat, vel illum</blockquote>
    </article>
    <article class="testimonial" style="top:372px">
      <div class="client"><div class="client-photo" role="img" aria-label="Portrait photo of client Daniel Reyes"></div><p class="client-name">Mr. Daniel Reyes</p></div>
      <blockquote class="quote">Lorem ipsum dolor sit amet, consectetuer adipiscing elit, sed diam nonummy nibh euismod tincidunt ut laoreet dolore magna aliquam erat volutpat. Ut wisi enim ad minim veniam, quis nostrud exerci tation ullamcorper suscipit lobortis nisl ut aliquip ex ea commodo consequat. Duis autem vel eum iriure dolor in hendrerit in vulputate velit esse molestie consequat, vel illum</blockquote>
    </article>

    <svg class="band" viewBox="0 0 480 100" aria-hidden="true">
      <defs><linearGradient id="bandRedR" x1="0" x2="1"><stop offset="0" stop-color="#7a0d1c"/><stop offset="1" stop-color="#9a1a2c"/></linearGradient></defs>
      <polygon points="0,38 480,38 480,100 0,100" fill="url(#bandRedR)"/>
      <polygon points="250,38 480,0 480,38" fill="#111"/>
    </svg>
    <p class="band-url">www.lumarinservices-example.com</p>
  </section>
</main>
</body>
</html>
```